BRINDLEWOOD EXTRA VIRGIN OLIVE OIL

I needs a design for an Australian Extra Virgin Olive Oil.

The label will go on a round clear bottle

The label size front and back is 145mm high x 60mm wide.

The important points for the design are as follows.

I want to see elegant olives on the label so that non English speaking markets can easily understand its olive oil. I want it too look classy . IT must also look Australian but I don't want to see kangaroos just colours that reflect Australia.

The mandatory info on front label will be

BRINDLEWOOD

Cold Pressed
EXTRA VIRGIN OLIVE OIL

AUSTRALIAN

1 litre

```html
<!DOCTYPE html>
<html lang="en">
<head>
<meta charset="utf-8">
<title>Brindlewood Extra Virgin Olive Oil – Label Designs</title>
<link rel="stylesheet" href="https://fonts.googleapis.com/css2?family=Open+Sans:ital,wght@0,400;0,600;1,800&display=swap">
<style>
  :root {
    --wattle-gold: #c9952f;
    --bush-green: #28301f;
    --label-white: #ffffff;
    --oil-silver: #e4e4e2;
    --page-bg: #ffffff;
    --leaf-light: #dfe3cf;
    --leaf-deep: #6f7a2e;
    --olive-dark: #3b3a22;
  }
  html, body {
    margin: 0;
    padding: 0;
    background: var(--page-bg);
    overflow: hidden;
  }
  .canvas {
    width: 1157px;
    height: 1200px;
    display: block;
  }
  .label-base { fill: var(--wattle-gold); }
  .label-body { fill: var(--bush-green); }
  .photo-frame { fill: none; stroke: var(--wattle-gold); stroke-width: 3.5; }
  .brand-name, .origin-name, .variety, .process, .volume {
    font-family: "Open Sans", "Segoe UI", sans-serif;
    fill: var(--label-white);
  }
  .brand-name { font-size: 12px; font-weight: 400; letter-spacing: 0.2px; }
  .variety { font-size: 20.5px; font-weight: 400; }
  .product-name {
    font-family: "Open Sans", "Segoe UI", sans-serif;
    font-size: 21px;
    font-weight: 800;
    font-style: italic;
    fill: var(--oil-silver);
    filter: drop-shadow(1px 1.5px 0.6px rgba(0,0,0,0.75));
  }
  .process { font-size: 9px; }
  .origin-name { font-size: 20px; font-weight: 400; }
  .volume { font-size: 8px; }
  .label-shadow { filter: drop-shadow(2px 3px 2.5px rgba(0,0,0,0.35)); }
</style>
</head>
<body>
<svg class="canvas" viewBox="0 0 457 474" xmlns="http://www.w3.org/2000/svg">
  <defs>
    <clipPath id="label-shape">
      <rect x="0" y="0" width="199" height="425" rx="12" ry="12"/>
    </clipPath>
    <linearGradient id="olive-branch-green" x1="0" y1="0" x2="1" y2="1">
      <stop offset="0" stop-color="var(--leaf-light)"/>
      <stop offset="0.55" stop-color="#a9ac5a"/>
      <stop offset="1" stop-color="var(--leaf-deep)"/>
    </linearGradient>
    <linearGradient id="olive-mixed-tones" x1="0" y1="0" x2="1" y2="1">
      <stop offset="0" stop-color="var(--leaf-light)"/>
      <stop offset="0.5" stop-color="#9a9e4c"/>
      <stop offset="1" stop-color="var(--olive-dark)"/>
    </linearGradient>
    <path id="brand-arc-a" d="M8,108 Q20,58 62,34"/>
    <path id="origin-arc-a" d="M10,418 Q95,398 186,338"/>
    <path id="brand-arc-b" d="M8,108 Q20,58 62,34"/>
    <path id="origin-arc-b" d="M10,418 Q95,398 186,338"/>
  </defs>

  <!-- Label: green olives -->
  <g class="label label-green-olives label-shadow" transform="translate(12,22)">
    <g clip-path="url(#label-shape)">
      <rect class="label-base" x="0" y="0" width="199" height="425"/>
      <path class="label-body" d="M0,112 Q70,40 199,26 L199,312 Q110,335 0,380 Z"/>
    </g>
    <g role="img" aria-label="Photograph of a green olive branch with ripe green olives">
      <rect x="52" y="22" width="101" height="93" fill="url(#olive-branch-green)"/>
    </g>
    <rect class="photo-frame" x="50" y="20" width="105" height="97"/>
    <text class="brand-name"><textPath href="#brand-arc-a">BRINDLEWOOD</textPath></text>
    <text class="variety" x="100" y="183" text-anchor="middle">EXTRA VIRGIN</text>
    <text class="product-name" x="97" y="216" text-anchor="middle">OLIVE OIL</text>
    <text class="process" x="100" y="262" text-anchor="middle">Cold Pressed</text>
    <text class="origin-name"><textPath href="#origin-arc-a">AUSTRALIAN</textPath></text>
    <text class="volume" x="188" y="413" text-anchor="end">1 litre</text>
  </g>

  <!-- Label: mixed olives -->
  <g class="label label-mixed-olives label-shadow" transform="translate(243,22)">
    <g clip-path="url(#label-shape)">
      <rect class="label-base" x="0" y="0" width="199" height="425"/>
      <path class="label-body" d="M0,112 Q70,40 199,26 L199,312 Q110,335 0,380 Z"/>
    </g>
    <g role="img" aria-label="Photograph of an olive branch with green and black olives">
      <rect x="52" y="22" width="101" height="93" fill="url(#olive-mixed-tones)"/>
    </g>
    <rect class="photo-frame" x="50" y="20" width="105" height="97"/>
    <text class="brand-name"><textPath href="#brand-arc-b">BRINDLEWOOD</textPath></text>
    <text class="variety" x="100" y="183" text-anchor="middle">EXTRA VIRGIN</text>
    <text class="product-name" x="97" y="216" text-anchor="middle">OLIVE OIL</text>
    <text class="process" x="100" y="262" text-anchor="middle">Cold Pressed</text>
    <text class="origin-name"><textPath href="#origin-arc-b">AUSTRALIAN</textPath></text>
    <text class="volume" x="188" y="413" text-anchor="end">1 litre</text>
  </g>
</svg>
</body>
</html>
```